Business Cards for new orthopaedic surgery practice

My husband and I are starting our own orthopaedic surgery practice. We are looking for a business card that is uniform, but one will have my name/title and the other will have his. You can just create one design with my name on it for now. But when I choose your design as the winning design I will ask that you add another copy with his name/title.

We are looking for classy, simple, elite all in one. We like dark blues/a little gold/yellow. Something that goes with our logo. We want our logo incorporated. Here is all the info you need:
Business name: RV Bone & Vitality Center
Location: 38517 North Willowmere Ave
Palm Haven, FL 33990
Phone: 954-218-4063
Fax: 954-582-7341
Email: info@myrvbonecare.example

Names: Lydia Vance, M.D.
Board Certified Hand and Upper Extremity Surgeon

Ebo Dansu, M.D.
Board Certified Hip & Knee Replacement/General Orthopaedic Surgeon

Can decide what you want to put on the back. Maybe a slogan:
Grounded in Care. Centered on You

I am just going to upload our logo. The only thing is if we select you as the winning design, the location, and phone numbers may change. We will need your help to update that once fully solidified.

Industry/Entity Type

Medical

Contact Information for Business Card

Colors
0054AA
0677BA
7BADD7
CADEEF
E8F1F8
0094D4
00A9DD
6FCCEA
C7EBF8
E9F6FB

Requirements
Must have
• class, appeal,
Should not have
• We want to air on the side of masculine if we are looking at masculine vs. feminine feel. But we still want it classy, sophisticated, and something we will love

```html
<!DOCTYPE html>
<html lang="en">
<head>
<meta charset="utf-8">
<title>RV Bone &amp; Vitality Center — Business Card</title>
<link href="https://fonts.googleapis.com/css2?family=Poppins:ital,wght@0,400;0,600;0,700;1,400&display=swap" rel="stylesheet">
<style>
  :root {
    --bg: #1c1d20;
    --paper: #ffffff;
    --navy: #233a8c;
    --deep: #0a1f7a;
    --royal: #0054AA;
    --cyan: #00A9DD;
    --sky: #1cb8dc;
    --ink-grey: #6b6e75;
    --faint: #e9ebf3;
    --white: #ffffff;
  }
  * { box-sizing: border-box; margin: 0; padding: 0; }
  html, body {
    width: 1200px; height: 900px; overflow: hidden;
    background: var(--bg);
    font-family: "Poppins", sans-serif;
  }
  .sheet {
    width: 1200px; height: 900px;
    display: flex; flex-direction: column;
    align-items: center; justify-content: center; gap: 40px;
  }
  .card {
    width: 700px; height: 400px;
    position: relative; overflow: hidden;
    box-shadow: 0 14px 34px rgba(0,0,0,.55);
  }

  /* Brand lockup */
  .brand { display: flex; align-items: center; gap: 16px; }
  .brand-mark { width: 24px; height: 24px; border-radius: 50%; flex: none; }
  .brand-divider { width: 2px; height: 82px; flex: none; }
  .brand-name {
    font-weight: 600; text-transform: uppercase;
    line-height: 1.08; letter-spacing: .5px;
  }

  /* Front */
  .card-front { background: var(--paper); }
  .card-front .brand { position: absolute; left: 44px; top: 40px; }
  .card-front .brand-mark { background: var(--navy); }
  .card-front .brand-divider { background: var(--navy); }
  .card-front .brand-name { color: var(--navy); font-size: 22px; }

  .contact {
    position: absolute; left: 44px; top: 172px;
    list-style: none; color: var(--ink-grey);
    font-size: 15px; line-height: 1.7;
  }
  .contact li { display: flex; align-items: center; gap: 9px; }
  .contact svg { width: 14px; height: 14px; fill: var(--cyan); flex: none; }

  .person { position: absolute; right: 52px; top: 150px; text-align: right; }
  .person-name { color: var(--cyan); font-weight: 700; font-size: 23px; letter-spacing: .3px; }
  .person-title { color: var(--ink-grey); font-style: italic; font-size: 15px; margin-top: 2px; }
  .accent-bar {
    position: absolute; right: 0; top: 214px;
    width: 26px; height: 34px; background: var(--cyan);
  }
  .faint-name {
    position: absolute; right: 40px; bottom: 18px;
    color: var(--faint); font-weight: 600; font-size: 40px;
    text-transform: uppercase; line-height: 1.05; text-align: right;
  }

  /* Back */
  .card-back {
    background:
      radial-gradient(ellipse 280px 220px at 0% 100%, rgba(255,255,255,.95), rgba(255,255,255,0) 70%),
      linear-gradient(160deg, var(--deep) 0%, var(--royal) 45%, var(--sky) 100%);
    display: flex; flex-direction: column; align-items: center; justify-content: center; gap: 34px;
  }
  .card-back .brand-mark { background: var(--white); width: 30px; height: 30px; }
  .card-back .brand-divider { background: var(--white); height: 110px; }
  .card-back .brand-name { color: var(--white); font-size: 30px; }
  .tagline { color: var(--white); font-size: 18px; letter-spacing: .5px; }
</style>
</head>
<body>
<main class="sheet">
  <section class="card card-front" aria-label="Business card front">
    <div class="brand">
      <span class="brand-mark"></span>
      <span class="brand-divider"></span>
      <span class="brand-name">RV Bone &amp;<br>Vitality<br>Center</span>
    </div>
    <ul class="contact">
      <li><svg viewBox="0 0 24 24"><path d="M6.6 10.8a15 15 0 0 0 6.6 6.6l2.2-2.2a1 1 0 0 1 1-.25 11.4 11.4 0 0 0 3.6.57 1 1 0 0 1 1 1V20a1 1 0 0 1-1 1A17 17 0 0 1 3 4a1 1 0 0 1 1-1h3.5a1 1 0 0 1 1 1c0 1.25.2 2.45.57 3.57a1 1 0 0 1-.25 1z"/></svg>954-218-4063</li>
      <li><svg viewBox="0 0 24 24"><path d="M6 3h10v5H6zM4 9h16a2 2 0 0 1 2 2v7h-4v3H6v-3H2v-7a2 2 0 0 1 2-2zm4 7v3h8v-3z"/></svg>954-582-7341</li>
      <li><svg viewBox="0 0 24 24"><path d="M3 5h18a1 1 0 0 1 1 1v12a1 1 0 0 1-1 1H3a1 1 0 0 1-1-1V6a1 1 0 0 1 1-1zm9 7.5L4 7.4V8l8 5 8-5v-.6z"/></svg>info@myrvbonecare.example</li>
      <li>38517 North Willowmere Ave</li>
      <li>Palm Haven, FL 33990</li>
    </ul>
    <span class="faint-name" aria-hidden="true">RV Bone &amp;<br>Vitality</span>
    <div class="person">
      <p class="person-name">Lydia Vance, M.D.</p>
      <p class="person-title">Hand and Upper Extremity Surgery</p>
    </div>
    <span class="accent-bar"></span>
  </section>

  <section class="card card-back" aria-label="Business card back">
    <div class="brand">
      <span class="brand-mark"></span>
      <span class="brand-divider"></span>
      <span class="brand-name">RV Bone &amp;<br>Vitality<br>Center</span>
    </div>
    <p class="tagline">Grounded in Care. Centered on You</p>
  </section>
</main>
</body>
</html>
```